Business Card for a Jewellery Brand

Business card for an upscale jewellery brand. Attached is the brand logo and icon and color board. I am looking for two card versions: one for the founder and one is generic. The card should be elegant and convey upscale and premium feel. I am open to both square and rectangle card shapes.

Industry/Entity Type

Jewelry

Contact Information for Business Card

Two cards: (1) Sunela Parvaniya (Founder) (2) General
(1) Sunela Parvaniya card should have Name: Sunela Parvaniya, Title: Founder Email id: sunela@quiremo.com.au. Phone no: +61452913307
(2) Generic card should have Email id: info@quiremo.com.au. Phone no: +61436207518

Requirements
Must have
• Workmark
• ICON
• Phone no
• Email ID
• ABN: 58219740312 (Note: ABN is Business number in Australia)
• Website: www.quiremo.com.au
• plain circle: quiremo_jewellery
• plain circle: @quiremojewellery
Nice to have
• Tagline

```html
<!DOCTYPE html>
<html lang="en">
<head>
<meta charset="utf-8">
<title>Quiremo — Business Cards</title>
<link rel="stylesheet" href="https://fonts.googleapis.com/css2?family=Montserrat:wght@400;600&family=Open+Sans:wght@400;600&display=swap">
<style>
  :root {
    --stage: #222222;
    --paper: #ffffff;
    --blush: #e5989a;
    --blush-deep: #e08f8f;
    --ink: #1d1d1d;
    --white: #ffffff;
  }
  * { margin: 0; padding: 0; box-sizing: border-box; }
  html, body { width: 1200px; height: 900px; overflow: hidden; }
  body {
    background: var(--stage);
    position: relative;
    font-family: "Open Sans", Arial, sans-serif;
  }
  .card {
    position: absolute;
    top: 306px;
    width: 440px;
    height: 271px;
    overflow: hidden;
  }
  .card--front { left: 149px; background: var(--paper); }
  .card--back { left: 608px; width: 441px; }

  /* front */
  .brand-mark {
    position: absolute;
    left: 52px;
    top: 150px;
    width: 150px;
    text-align: center;
    font-family: "Montserrat", Arial, sans-serif;
    font-weight: 400;
    font-size: 27px;
    letter-spacing: 4px;
    color: var(--blush);
  }
  .divider {
    position: absolute;
    left: 221px;
    top: 80px;
    width: 1px;
    height: 110px;
    background: var(--blush);
  }
  .details {
    position: absolute;
    left: 239px;
    top: 77px;
    font-size: 12px;
    color: var(--ink);
    line-height: 1;
  }
  .details__name {
    font-family: "Montserrat", Arial, sans-serif;
    font-weight: 600;
    font-size: 14.5px;
    color: var(--blush);
    text-transform: uppercase;
    letter-spacing: 0.2px;
    margin-bottom: 6px;
  }
  .details__role { margin-bottom: 8px; }
  .details__abn { margin-bottom: 16px; }
  .details__abn-label { color: var(--blush); font-weight: 600; }
  .contact-list { list-style: none; }
  .contact-list li {
    display: flex;
    align-items: center;
    height: 16px;
  }
  .contact-list svg {
    width: 9px;
    height: 9px;
    margin-right: 5px;
    margin-left: -1px;
    fill: var(--blush);
  }

  /* back */
  .back-texture {
    position: absolute;
    inset: 0;
    background: linear-gradient(180deg, var(--blush) 0%, var(--blush-deep) 100%);
  }
  .back-wordmark {
    position: absolute;
    left: 0;
    right: 0;
    top: 108px;
    text-align: center;
    font-family: "Montserrat", Arial, sans-serif;
    font-weight: 400;
    font-size: 42px;
    letter-spacing: 8px;
    color: var(--white);
  }
  .social-row {
    position: absolute;
    left: 107px;
    top: 203px;
    width: 228px;
    height: 18px;
  }
  .social-row__rule {
    position: absolute;
    top: 9px;
    height: 1px;
    background: rgba(255,255,255,0.8);
  }
  .social-row__rule--left { left: 0; width: 85px; }
  .social-row__rule--right { right: 0; width: 85px; }
  .social-row__dot {
    position: absolute;
    top: 0;
    width: 18px;
    height: 18px;
    border-radius: 50%;
    background: var(--white);
  }
  .social-row__dot--first { left: 92px; }
  .social-row__dot--second { left: 116px; }
  .social-handle {
    position: absolute;
    left: 0;
    right: 0;
    top: 229px;
    text-align: center;
    font-size: 12px;
    color: var(--white);
  }
</style>
</head>
<body>
  <section class="card card--front" aria-label="Founder card front">
    <div class="brand-mark">QUIREMO</div>
    <div class="divider"></div>
    <div class="details">
      <p class="details__name">Sunela Parvaniya</p>
      <p class="details__role">Founder</p>
      <p class="details__abn"><span class="details__abn-label">ABN:</span> 58219740312</p>
      <ul class="contact-list">
        <li>
          <svg viewBox="0 0 10 10" aria-hidden="true"><path d="M2 0.5 L3.6 2.6 L2.8 3.6 Q4 6 6.4 7.2 L7.4 6.4 L9.5 8 L8.4 9.5 Q4.5 9.5 2 6.8 Q0.3 4.6 0.5 1.6 Z"/></svg>
          +61452913307
        </li>
        <li>
          <svg viewBox="0 0 10 10" aria-hidden="true"><path d="M0.5 2 H9.5 V8.5 H0.5 Z M0.5 2 L5 5.5 L9.5 2" /></svg>
          sunela@quiremo.com.au.
        </li>
        <li>
          <svg viewBox="0 0 10 10" aria-hidden="true"><circle cx="5" cy="5" r="4.5"/></svg>
          www.quiremo.com.au
        </li>
      </ul>
    </div>
  </section>

  <section class="card card--back" aria-label="Card back">
    <div class="back-texture" role="img" aria-label="Faint repeating brand pattern on blush pink"></div>
    <div class="back-wordmark">QUIREMO</div>
    <div class="social-row">
      <span class="social-row__rule social-row__rule--left"></span>
      <span class="social-row__dot social-row__dot--first"></span>
      <span class="social-row__dot social-row__dot--second"></span>
      <span class="social-row__rule social-row__rule--right"></span>
    </div>
    <p class="social-handle">@quiremojewellery</p>
  </section>
</body>
</html>
```